SaaS / Consulting / Solution website redesign

We need a website design that:
- Is completely different than our current design : https://plumvessel.net
- Has a very minimal amount of copy
- Changes our positioning from a SaaS application to a solutions company. Solutions company means that we help our customers solve their problems with consulting, training, and tools. An example of a solutions company is here: https://oldpages.example/web/20130111103320/http://www.brindlework.com:80/
- Does not make us look like a start up
- Is more people oriented than technology oriented

We need a designer that:
- Is a rebel at heart
- Is a minimalist
- Tells us why our current site sucks
- Can disagree with us
- Can also do copywriting or already has a copywriter that can help
- Is ok with saying we have capability that we don't in order to see if people actually want that
- Can understand the difference between our grand vision and where we need to focus ourselves today in order to get there

Who we are:
- Entrepreneurs
- Programmers
- Consultants
- Investors

Here's our design goals:
#1 Get customers, investors, employers, and partners excited about our unique and clearly articulated value proposition
#2 Get people to contact us asking for help with their programs
#3 Position ourselves as an expert in the skills based volunteering, mentorship, and group collaboration
#4 Make it easy for people, who already know who we are, to register online

What our grand vision is:
- Create a marketplace where any person can go to our site and find time with anyone they need to meet with. Whether that is their hair stylist, school advisor, parent of your kids class, dentist, attorney, etc.

What will you get if you win:
- In addition to the prize of this project we will have many landing pages and other revisions we will need in the future. We currently don't have a designer or copywriter and need to add that capability to our team

Who do we need to appeal to:
- Directors that are launching innovative programs inside organizations
- IT personnel who are trying to disqualify our technology so they don't have to support it or deal with it when it doesn't go well
- Enterprise IT architects who don't want our product being on its own island within their organization totally incompatible with everything else. Architects which are trying to assess how our platform will co-exist with all their other platforms
- Vice Presidents who want to help their directors understand that we don't have enough experience to help them
- Program managers who have to juggle a million things and need a tool that actually helps instead of confuses them and adds more work for them.
- Program managers & directors that have been given ambiguous goals by their board of directors like "improve retention, increase engagement, create innovation, get people to collaborate." And who have no idea where to start or how to deliver on things like that.
- Program managers, directors, and vice presidents that are trying to understand how our technology and services fit into their existing technology and capability
- Employees who are bored and uninspired with their current tools and are hoping for some excitement in their life. Kind of like candy or a double espresso.
- Investors who think, our company like all the rest, are going to waste their money and make them look like a fool

Other information:
-The CSS and html needs to be responsive

-Our registration onboarding flow needs to collect this information:
User first name
user last name
user email
(verify their email)
user phone number
(verify their phone number)
User profile image (optional)
User profile summary (optional, like a bio, freeform text fiels)
If applicable: Register their organization
Organization name
Organization image (optional)
Account Mailing address
account Billing address (could be same as mailing address)
account Billing email address (could be same as user address)
account Product selection (pricing tier)
account Credit card information

The designs I am getting are a good start but they are only the front page. I just want you to know that I am expecting and need more than a landing page to complete the design. I will likely need a page that outlines the benefits and features of the product itself, how its different than our competitors, which will not be on the front page. I will need a registration flow. I will need a blog page design so we can post blog articles, I will need a team page, a page that goes into detail on our training, our services. I will likely need a page that shows all news and media we have been in. I need to show customer and user quotes, case studies, a way to contact us, partners, general resources like on collaboration, product tutorials, customers. I need the site to address a comprehensive set of needs. I need that design to be consistent and thorough. I know what PlateHarbor is. I'm not using because I need more than a template that was customized. I need to be unique and match our brand thoughtfully, beautifully, and artistically. Someone asked me a question about how Murmly is similar to our tool in the way it is referred by end users and purchased by managers. Our website needs to primarily talk to the managers as I explained in the brief but it needs to appear cool and exciting to our end-users without focusing on the technology too much. Murmly is a tool that teams use to collaborate in small and large enterprises. The value prop for them is that communication is easier. But they don't put that on their website. Why? Because the users of the technology won't go to the website to find out information on it, they get their information from someone who is using it and demos it to them. When Ines tells her manager Otto "Lets get murmly, Ruth is using it at her company and its great" Ines's manager doesn't know anything about murmly so she promptly googles it. The most important thing from Ines's perspective is that Otto agrees to try it out. Otto's biggest concern is that productivity will be enhanced to degraded. Murmly knows this and so on the front page they know they are talking to Otto NOT Ines because Ines is already sold on it and doesn't need to get sold on the website. Ines is end user. Otto is the purchaser. We have the same problem and so our end users are not the ones purchasing our product, their managers are purchasing our product. We get referred by our end users and vetted by their managers. Hope this helps! Thank you for looking at this project!  Added Wednesday, June 7, 2017

Another observation I am having about the designs being submitted. I believe we used the animations on our current website because animations / cartoons connect with the "inner child" in our users. Whatever that means :-). I think it's what makes our brand fun. I have a hard time imagining that we could make the design fun looking without animations but I'm sure it can be achieved. I also recognize that blending pictures of real people and animations is hard. So either we must masterfully blend them, use only animations, or make the real people have a LOT of fun! So far most of the designs while achieve the goal of appealing to the serious Vice Presidents and directors, they are not doing a good job at appealing to the overworked program managers and bored employees. There seems to stand another challenge with animations which is animations are hard to find and/or create that achieve the message / emotion we are trying to communicate. I don't have any good answers for this but I will say we can hire both animators and illustrators if we need to. All you have to do is communicate the effect in the website design with some simpler version maybe not the end illustration or animation itself. Added Wednesday, June 7, 2017

• Sex appeal and a sense of humor. Copy that makes people excited and clairvoyant about our potential.
• Boring renditions of other non-inspiring websites

```html
<!DOCTYPE html>
<html lang="en">
<head>
<meta charset="utf-8">
<title>Tidewell — Connecting People</title>
<link href="https://fonts.googleapis.com/css2?family=Lato:wght@300;400;700;900&family=Open+Sans:wght@400;700&display=swap" rel="stylesheet">
<style>
:root{
  --green:#72c47a;
  --green-dark:#5fae67;
  --red:#e94f4f;
  --ink:#333333;
  --muted:#666666;
  --rule:#dddddd;
  --panel:#f1f1f1;
  --footer:#272e3d;
  --white:#ffffff;
}
*{margin:0;padding:0;box-sizing:border-box}
html,body{width:1200px;height:2835px;overflow:hidden}
body{font-family:"Lato",sans-serif;color:var(--ink);background:var(--white);position:relative}
.abs{position:absolute}

/* header */
.site-header{position:absolute;left:0;top:0;width:1200px;height:85px;background:var(--white)}
.brand{position:absolute;left:132px;top:16px;font-size:40px;font-weight:400;color:var(--green);letter-spacing:-0.5px}
.main-nav{position:absolute;left:363px;top:31px;display:flex;gap:0}
.main-nav a{font-size:11px;font-weight:700;color:var(--ink);text-decoration:none;text-transform:uppercase;padding:7px 10px;margin-right:26px}
.main-nav a.is-active{background:var(--red);color:var(--white)}
.call{position:absolute;left:918px;top:25px}
.call-icon{position:absolute;left:0;top:2px;width:30px;height:30px;border-radius:50%;background:var(--green)}
.call-icon svg{position:absolute;left:8px;top:8px}
.call-label{position:absolute;left:44px;top:0;font-size:9px;font-weight:700;white-space:nowrap}
.call-number{position:absolute;left:44px;top:12px;font-size:21px;color:var(--red);white-space:nowrap}

/* hero */
.hero{position:absolute;left:0;top:85px;width:1200px;height:558px;
  background:linear-gradient(100deg,#3d3a3a 0%,#6f6864 30%,#c9c4bf 55%,#9fb4cf 70%,#d8dde2 85%,#5a5a5e 100%)}
.hero-arrow{position:absolute;width:44px;height:44px;border-radius:50%}
.hero-arrow svg{position:absolute;left:14px;top:14px}
.hero-arrow.prev{left:67px;top:250px;background:#1e1e1e}
.hero-arrow.next{left:1112px;top:250px;background:var(--green-dark)}
.hero-title{position:absolute;left:108px;top:365px;color:var(--white);font-size:58px;line-height:64px;text-transform:uppercase}
.hero-title b{font-weight:900;display:block}
.hero-title span{font-weight:300;display:block}

/* section titles */
.section-title{position:absolute;left:0;width:1200px;text-align:center;font-size:23px;font-weight:700;color:var(--red);text-transform:uppercase}
.section-rule{position:absolute;left:567px;width:66px;height:2px;background:var(--rule)}

/* who we are */
.intro{position:absolute;left:225px;top:797px;width:750px;text-align:center;font-size:14.5px;line-height:24px;color:var(--ink)}
.role{position:absolute;top:888px;width:163px;height:187px;text-align:center}
.role svg{position:absolute;left:52px;top:18px}
.role-name{position:absolute;left:0;top:112px;width:100%;font-size:17px;color:var(--ink)}
.role.is-featured{background:var(--green)}
.read-more{display:inline-block;font-size:10px;font-weight:700;text-transform:uppercase;background:#d8efda;color:var(--ink);padding:5px 10px}
.role .read-more{position:absolute;left:40px;top:148px}

/* services */
.services{position:absolute;left:0;top:1143px;width:1200px;height:602px;background:var(--panel)}
.service{position:absolute;top:1327px;width:330px;text-align:center}
.service-ring{position:absolute;left:80px;top:0;width:170px;height:170px;border-radius:50%;background:var(--panel);box-shadow:0 4px 8px rgba(0,0,0,0.12)}
.service-ring svg{position:absolute;left:50px;top:50px}
.service h3{position:absolute;left:0;top:221px;width:100%;font-size:19px;font-weight:400;color:var(--ink)}
.service p{position:absolute;left:45px;top:263px;width:240px;font-size:14px;line-height:21px;color:var(--ink)}
.service-divider{position:absolute;top:1332px;width:1px;height:350px;background:#dcdcdc}

/* blog */
.post{position:absolute;top:1941px;width:297px;height:402px;border:1px solid #e3e3e3;background:var(--white)}
.post-image{position:absolute;left:0;top:0;width:295px;height:222px}
.post h4{position:absolute;left:25px;top:250px;width:250px;font-family:"Open Sans",sans-serif;font-size:12.5px;line-height:17px;font-weight:700;text-transform:uppercase;color:#111}
.post p{position:absolute;left:25px;top:295px;width:250px;font-size:12px;line-height:18px;color:var(--muted)}
.post .read-more{position:absolute;left:25px;top:359px;background:var(--green);color:var(--white);padding:7px 8px}

/* footer */
.site-footer{position:absolute;left:0;top:2413px;width:1200px;height:422px;background:var(--footer);color:var(--white)}
.footer-brand{position:absolute;left:142px;top:64px;font-size:40px;color:var(--green)}
.follow{position:absolute;left:169px;top:148px;width:120px;text-align:center;font-size:11px;font-weight:700;text-transform:uppercase}
.social{position:absolute;left:180px;top:182px;display:flex;gap:7px}
.social i{display:block;width:20px;height:20px;border-radius:50%}
.footer-heading{position:absolute;top:72px;font-size:11px;font-weight:700;text-transform:uppercase;white-space:nowrap}
.contact-row{position:absolute;left:386px;font-size:11px;line-height:19px;color:#d9dce2}
.contact-row svg{position:absolute;left:0;top:3px}
.contact-row span{display:block;margin-left:24px}
.footer-menu{position:absolute;left:650px;top:105px;list-style:none}
.footer-menu li{font-size:11px;line-height:23px;color:#d9dce2}
.newsletter-input{position:absolute;left:835px;top:108px;width:235px;height:50px;background:var(--white);color:#666;font-size:11px}
.newsletter-input svg{position:absolute;left:20px;top:20px}
.newsletter-input span{position:absolute;left:48px;top:18px}
.signup{position:absolute;left:968px;top:174px;width:102px;height:34px;background:var(--red);color:var(--white);font-size:14px;font-weight:700;text-align:center;line-height:34px;text-transform:uppercase}
.footer-rule{position:absolute;left:132px;top:307px;width:936px;height:1px;background:#3a4254}
.copyright{position:absolute;left:0;top:351px;width:1200px;text-align:center;font-size:11px;color:#d9dce2}
</style>
</head>
<body>

<header class="site-header">
  <div class="brand">Tidewell</div>
  <nav class="main-nav">
    <a class="is-active">Home</a>
    <a>Who we are</a>
    <a>Services</a>
    <a>Blog</a>
    <a>Contact us</a>
  </nav>
  <div class="call">
    <div class="call-icon"><svg width="14" height="14" viewBox="0 0 24 24"><path fill="#fff" d="M6.6 10.8a15.1 15.1 0 0 0 6.6 6.6l2.2-2.2c.3-.3.7-.4 1-.2 1.1.4 2.3.6 3.6.6.6 0 1 .4 1 1V20c0 .6-.4 1-1 1A17 17 0 0 1 3 4c0-.6.4-1 1-1h3.5c.6 0 1 .4 1 1 0 1.3.2 2.5.6 3.6.1.3 0 .7-.2 1z"/></svg></div>
    <div class="call-label">CALL US :</div>
    <div class="call-number">555.010.2040</div>
  </div>
</header>

<section class="hero" role="img" aria-label="Photo of a smiling consultant in a blue shirt meeting with a client across an office desk">
  <div class="hero-arrow prev"><svg width="16" height="16" viewBox="0 0 16 16"><path d="M10 3 5 8l5 5" stroke="#fff" stroke-width="2" fill="none"/></svg></div>
  <div class="hero-arrow next"><svg width="16" height="16" viewBox="0 0 16 16"><path d="M6 3l5 5-5 5" stroke="#fff" stroke-width="2" fill="none"/></svg></div>
  <h1 class="hero-title"><b>Connecting</b><span>People</span></h1>
</section>

<h2 class="section-title" style="top:704px">Who we are</h2>
<div class="section-rule" style="top:755px"></div>
<p class="intro">Bunkshare and Ridelane turned underutilized homes and vehicles into an income source and creating nearly $100B in value for investors. Underutilized time is an even more valuable resource than cars and homes.</p>

<div class="role" style="left:214px">
  <svg width="60" height="70" viewBox="0 0 60 70"><circle cx="30" cy="18" r="12" fill="#72c47a"/><path d="M8 66c0-18 10-28 22-28s22 10 22 28z" fill="#72c47a"/><path d="M28 40h4l2 20-4 4-4-4z" fill="#fff"/></svg>
  <div class="role-name">Entrepreneurs</div>
</div>
<div class="role is-featured" style="left:425px">
  <svg width="60" height="70" viewBox="0 0 60 70"><circle cx="30" cy="16" r="11" fill="#2f3a33"/><path d="M12 46c0-12 8-18 18-18s18 6 18 18z" fill="#2f3a33"/><rect x="10" y="44" width="40" height="22" rx="2" fill="#2f3a33"/><rect x="26" y="52" width="8" height="6" fill="#72c47a"/></svg>
  <div class="role-name">Programmers</div>
  <span class="read-more">Read more</span>
</div>
<div class="role" style="left:649px">
  <svg width="60" height="70" viewBox="0 0 60 70"><circle cx="30" cy="20" r="12" fill="#72c47a"/><path d="M16 20a14 14 0 0 1 28 0" stroke="#72c47a" stroke-width="3" fill="none"/><rect x="13" y="18" width="5" height="9" rx="2" fill="#72c47a"/><rect x="42" y="18" width="5" height="9" rx="2" fill="#72c47a"/><path d="M8 66c0-18 10-28 22-28s22 10 22 28z" fill="#72c47a"/></svg>
  <div class="role-name">Consultants</div>
</div>
<div class="role" style="left:855px">
  <svg width="60" height="70" viewBox="0 0 60 70"><circle cx="22" cy="20" r="11" fill="#72c47a"/><path d="M2 66c0-17 9-26 20-26s20 9 20 26z" fill="#72c47a"/><text x="42" y="22" font-family="Lato, sans-serif" font-weight="700" font-size="20" fill="#72c47a">$</text><rect x="38" y="52" width="5" height="14" fill="#72c47a"/><rect x="45" y="46" width="5" height="20" fill="#72c47a"/><rect x="52" y="40" width="5" height="26" fill="#72c47a"/></svg>
  <div class="role-name">Investors</div>
</div>

<section class="services"></section>
<h2 class="section-title" style="top:1201px">Our services</h2>
<div class="section-rule" style="top:1250px"></div>
<div class="service-divider" style="left:423px"></div>
<div class="service-divider" style="left:784px"></div>

<div class="service" style="left:83px">
  <div class="service-ring"><svg width="70" height="70" viewBox="0 0 70 70"><circle cx="26" cy="22" r="11" fill="#72c47a"/><path d="M4 66c0-17 10-26 22-26s22 9 22 26z" fill="#72c47a"/><path d="M42 6h24v16H52l-6 5v-5h-4z" fill="none" stroke="#72c47a" stroke-width="2.5"/><circle cx="49" cy="14" r="1.6" fill="#72c47a"/><circle cx="54" cy="14" r="1.6" fill="#72c47a"/><circle cx="59" cy="14" r="1.6" fill="#72c47a"/></svg></div>
  <h3>Consulting</h3>
  <p>Tidewell is going to help everyone with a computer or smartphone connect in person by helping them find time to meet</p>
</div>
<div class="service" style="left:436px">
  <div class="service-ring"><svg width="70" height="70" viewBox="0 0 70 70"><circle cx="14" cy="16" r="7" fill="#72c47a"/><rect x="7" y="25" width="14" height="26" rx="3" fill="#72c47a"/><rect x="8" y="50" width="5" height="16" fill="#72c47a"/><rect x="15" y="50" width="5" height="16" fill="#72c47a"/><rect x="28" y="12" width="38" height="28" fill="none" stroke="#72c47a" stroke-width="3"/><path d="M32 34l8-8 6 5 10-11" fill="none" stroke="#72c47a" stroke-width="2.5"/><path d="M47 40v8M47 48l-10 18M47 48l10 18" stroke="#72c47a" stroke-width="3"/></svg></div>
  <h3>Training</h3>
  <p>Tidewell is going to help everyone with a computer or smartphone connect in person by helping them find time to meet</p>
</div>
<div class="service" style="left:789px">
  <div class="service-ring"><svg width="70" height="70" viewBox="0 0 70 70"><path d="M25 18v-6h20v6" fill="none" stroke="#72c47a" stroke-width="4"/><rect x="6" y="18" width="58" height="42" rx="5" fill="#72c47a"/><rect x="6" y="34" width="58" height="3" fill="#fff"/><rect x="30" y="30" width="10" height="10" rx="1" fill="#fff"/></svg></div>
  <h3>Tools</h3>
  <p>Tidewell is going to help everyone with a computer or smartphone connect in person by helping them find time to meet</p>
</div>

<h2 class="section-title" style="top:1825px">Latest blog</h2>
<div class="section-rule" style="top:1877px"></div>

<article class="post" style="left:127px">
  <div class="post-image" role="img" aria-label="Photo of a business team collaborating around a meeting table" style="background:linear-gradient(135deg,#e9ecef,#9aa3ad 55,#2d333b)"></div>
  <h4>Contrary to popular belief lorem ipsum</h4>
  <p>page editors now use Lorem ipsum as their default model text, and a search</p>
  <span class="read-more">Read more</span>
</article>
<article class="post" style="left:448px">
  <div class="post-image" role="img" aria-label="Photo of a smiling mentor talking with a colleague in a bright office" style="background:linear-gradient(135deg,#dfe5e8,#a9b6bd 50%,#c8a9b3)"></div>
  <h4>It is a long established fact that a reader</h4>
  <p>page editors now use Lorem ipsum as their default model text, and a search</p>
  <span class="read-more">Read more</span>
</article>
<article class="post" style="left:767px">
  <div class="post-image" role="img" aria-label="Photo of a cheerful group meeting with a client across a desk" style="background:linear-gradient(135deg,#c9dcc0,#8fa3b8 50%,#303744)"></div>
  <h4>Lorem ipsum is simply dummy text of the printing</h4>
  <p>page editors now use Lorem ipsum as their default model text, and a search</p>
  <span class="read-more">Read more</span>
</article>

<footer class="site-footer">
  <div class="footer-brand">Tidewell</div>
  <div class="follow">Follow us</div>
  <div class="social">
    <i style="background:#3b5a9a"></i><i style="background:#1da1f2"></i><i style="background:#dd4b39"></i><i style="background:#4c78b8"></i>
  </div>

  <div class="footer-heading" style="left:386px">Contact us</div>
  <div class="contact-row" style="top:111px">
    <svg width="10" height="13" viewBox="0 0 10 13"><path d="M5 0a5 5 0 0 1 5 5c0 3.5-5 8-5 8S0 8.5 0 5a5 5 0 0 1 5-5z" fill="#d9dce2"/><circle cx="5" cy="5" r="2" fill="#272e3d"/></svg>
    <span>1480 Larkmoor Avenue<br>Fairhaven, CA 95000</span>
  </div>
  <div class="contact-row" style="top:165px">
    <svg width="12" height="12" viewBox="0 0 24 24"><path fill="#d9dce2" d="M6.6 10.8a15.1 15.1 0 0 0 6.6 6.6l2.2-2.2c.3-.3.7-.4 1-.2 1.1.4 2.3.6 3.6.6.6 0 1 .4 1 1V20c0 .6-.4 1-1 1A17 17 0 0 1 3 4c0-.6.4-1 1-1h3.5c.6 0 1 .4 1 1 0 1.3.2 2.5.6 3.6.1.3 0 .7-.2 1z"/></svg>
    <span>555.010.2040</span>
  </div>
  <div class="contact-row" style="top:207px">
    <svg width="12" height="10" viewBox="0 0 12 10"><rect width="12" height="10" fill="#d9dce2"/><path d="M0 0l6 5 6-5" stroke="#272e3d" fill="none"/></svg>
    <span>info@tidewell.example</span>
  </div>

  <div class="footer-heading" style="left:650px">Menu</div>
  <ul class="footer-menu">
    <li>Home</li><li>Who we are</li><li>Services</li><li>Blog</li><li>Contact us</li>
  </ul>

  <div class="footer-heading" style="left:834px">Newsletter signup!</div>
  <div class="newsletter-input">
    <svg width="12" height="10" viewBox="0 0 12 10"><rect x=".5" y=".5" width="11" height="9" fill="none" stroke="#777"/><path d="M.5.5l5.5 4.5 5.5-4.5" stroke="#777" fill="none"/></svg>
    <span>E mail id</span>
  </div>
  <div class="signup">Signup!</div>

  <div class="footer-rule"></div>
  <div class="copyright">Copyrights @ 2017 All Rights Reserved</div>
</footer>

</body>
</html>
```